TALMORK

The business want a professional looking business card. We have a scetch we will add but want the extra upgrade, and would like more suggestions for variations of our business cards.

```html
<!DOCTYPE html>
<html lang="en">
<head>
<meta charset="utf-8">
<title>TALMORK Business Card</title>
<link rel="stylesheet" href="https://fonts.googleapis.com/css2?family=Marcellus&family=Montserrat:wght@400;500&display=swap">
<style>
  :root {
    --bg-light: #eeeeec;
    --bg-dark: #d9d9d6;
    --gold-cream: #e9dfb8;
    --gold-mid: #c2a866;
    --gold-deep: #9c8040;
    --gold-back: #a88e4a;
    --ink: #6a4f1c;
    --ink-soft: #7d6330;
    --edge: #6e5420;
  }
  * { margin: 0; padding: 0; box-sizing: border-box; }
  html, body { width: 1200px; height: 801px; overflow: hidden; }
  body {
    background: radial-gradient(ellipse at 40% 40%, var(--bg-light), var(--bg-dark));
    font-family: "Montserrat", sans-serif;
    position: relative;
  }
  .card {
    position: absolute;
    top: 258px;
    width: 500px;
    height: 286px;
    border-bottom: 3px solid var(--edge);
    box-shadow: 0 14px 28px rgba(0,0,0,0.18);
  }
  .card-front {
    left: 70px;
    background: linear-gradient(110deg, var(--gold-cream) 0%, var(--gold-mid) 55%, var(--gold-deep) 100%);
  }
  .card-back {
    left: 630px;
    background: var(--gold-back);
    display: flex;
    flex-direction: column;
    align-items: center;
    justify-content: center;
  }
  .brand-mark {
    position: absolute;
    top: 34px;
    right: 40px;
    text-align: center;
    color: var(--ink);
  }
  .brand-mark .brand-name {
    font-size: 15px;
    font-weight: 500;
    letter-spacing: 4px;
  }
  .brand-mark .brand-since {
    font-size: 6px;
    letter-spacing: 2px;
    margin-top: 3px;
  }
  .brand-mark .brand-dot {
    width: 30px; height: 30px;
    border-radius: 50%;
    background: var(--ink);
    margin: 0 auto 8px;
  }
  .identity {
    position: absolute;
    left: 36px;
    top: 96px;
    color: var(--ink);
  }
  .identity .full-name {
    font-family: "Marcellus", serif;
    font-size: 23px;
    letter-spacing: 1px;
  }
  .identity .role {
    font-size: 17px;
    margin-top: 4px;
  }
  .identity .alias {
    font-size: 9px;
    color: var(--ink-soft);
    margin-top: 3px;
  }
  .contacts {
    position: absolute;
    left: 36px;
    top: 196px;
    list-style: none;
    color: var(--ink);
    font-size: 13px;
  }
  .contacts li {
    display: flex;
    align-items: center;
    gap: 8px;
    height: 22px;
  }
  .contacts svg { width: 13px; height: 13px; fill: var(--ink); }
  .back-name {
    font-size: 44px;
    font-weight: 500;
    letter-spacing: 12px;
    color: var(--ink);
    padding-left: 12px;
  }
  .back-since {
    font-size: 13px;
    letter-spacing: 6px;
    color: var(--ink-soft);
    margin-top: 6px;
  }
</style>
</head>
<body>
  <section class="card card-front">
    <div class="brand-mark">
      <div class="brand-dot"></div>
      <div class="brand-name">TALMORK</div>
      <div class="brand-since">SINCE 2026</div>
    </div>
    <div class="identity">
      <div class="full-name">TALMORK HOLTBERG</div>
      <div class="role">CEO &amp; Founder</div>
      <div class="alias">Aren Holt Vikstad</div>
    </div>
    <ul class="contacts">
      <li>
        <svg viewBox="0 0 16 16" aria-hidden="true"><path d="M3 1h3l1.5 4-2 1.2a9 9 0 0 0 4.3 4.3L11 8.5l4 1.5v3a2 2 0 0 1-2 2A12 12 0 0 1 1 3a2 2 0 0 1 2-2z"/></svg>
        <span>004791234567</span>
      </li>
      <li>
        <svg viewBox="0 0 16 16" aria-hidden="true"><path d="M1 3h14v10H1z M2 4l6 5 6-5" fill="none" stroke="#6a4f1c" stroke-width="1.5"/></svg>
        <span>talmork.llc@postmail.com</span>
      </li>
      <li>
        <svg viewBox="0 0 16 16" aria-hidden="true"><circle cx="8" cy="8" r="6.5" fill="none" stroke="#6a4f1c" stroke-width="1.4"/><path d="M1.5 8h13M8 1.5c-3 3.5-3 9.5 0 13M8 1.5c3 3.5 3 9.5 0 13" fill="none" stroke="#6a4f1c" stroke-width="1.2"/></svg>
        <span>www.talmork.llc</span>
      </li>
    </ul>
  </section>

  <section class="card card-back">
    <div class="back-name">TALMORK</div>
    <div class="back-since">SINCE 2026</div>
  </section>
</body>
</html>
```